Website redesign for KestrelFinanceMan/TKFinanceMan

Job Title: Talented Web Designer for SEO-Friendly Website Creation & HostFalcon cPanel Integration
 
Inspiration: dunewheelracingexample.com
Pages:

About
Get a Quote
FAQ
Boat Loans
RV Loans
Testimonials
News/Blog
Affiliate Program
Contact

Job Description:
 
We are seeking a skilled and creative freelance web designer to build a stunning, SEO-optimized website for our business. The ideal candidate will have a strong design portfolio, technical expertise in creating search engine-friendly websites, and experience implementing websites into HostFalcon cPanel.
 
Project Overview:
 
Objective: Create a modern, motorsports themed visually appealing website that is optimized for SEO.

Platform: The site will be hosted on HostFalcon, so familiarity with their cPanel for setup and integration is essential.

Deliverables:
         •A fully functional website (desktop and mobile) with user-friendly navigation and a responsive design.
         •SEO best practices implemented throughout, including proper meta tags, optimized images, fast loading speeds, and mobile compatibility.
         •Seamless integration into HostFalcon cPanel for hosting.
         •Guidance or documentation on maintaining the site post-launch.
 
Key Skills Required:
 
         •Proficiency in web design (HTML, CSS, JavaScript, or relevant platforms like WordPress).
         •Knowledge of SEO principles and tools for website optimization.
         •Experience with HostFalcon cPanel, including file management and DNS settings.
         •Strong communication skills to understand our vision and provide progress updates.
 
What We’re Looking For:
 
         •A designer who can transform our ideas into a sleek and functional website.
         •Someone proactive in suggesting creative design elements and SEO improvements.
         •A reliable professional who can meet deadlines and deliver a polished product.
 
Please provide:
 
         1.A brief introduction and why you’re a good fit for this project.
         2.Examples of previous web design projects, especially those with SEO implementation.
         3.Your estimated timeline and cost for this project.
 
We are excited to work with a talented designer who can bring our vision to life. If you are passionate about web design and SEO, we’d love to hear from you!

Target Market(s)

Boat and RV buyers looking for a loan

Coding

Coded - Design and coding required

Number of Pages Required

5+ page

Colors
F0912C
F2A743
F7CA91
FBE8D2
FDF5EE

Requirements
Must have
• motorsports type design
Nice to have
• fcontact forms easy to use layout on brand and color scheme of kestrelfinanceman and tkfinanceman.example

```html
<!DOCTYPE html>
<html lang="en">
<head>
<meta charset="UTF-8">
<title>TKFinanceMan — Boat &amp; RV Loans</title>
<link rel="stylesheet" href="https://fonts.googleapis.com/css2?family=Poppins:wght@400;500;600;800;900&display=swap">
<style>
  :root {
    --orange: #F0912C;
    --orange-mid: #F2A743;
    --peach: #F7CA91;
    --cream: #FBE8D2;
    --ivory: #FDF5EE;
    --ink: #1d1d24;
    --white: #ffffff;
    --sky-top: #a9b4ea;
    --sky-pink: #e7a3cf;
    --sky-glow: #f3b8c8;
    --sea-far: #6f87b8;
    --sea-mid: #2f5680;
    --sea-deep: #1a3652;
  }
  * { margin: 0; padding: 0; box-sizing: border-box; }
  html, body { width: 1200px; height: 801px; overflow: hidden; background: var(--white); }
  body { font-family: "Poppins", sans-serif; color: var(--ink); }

  .site { position: relative; width: 1200px; height: 801px; overflow: hidden; }

  .hero-photo {
    position: absolute; inset: 0;
    background:
      radial-gradient(ellipse 420px 160px at 640px 470px, rgba(255,255,255,.55), transparent 70%),
      radial-gradient(ellipse 260px 90px at 880px 390px, rgba(240,200,225,.6), transparent 70%),
      linear-gradient(180deg, var(--sky-top) 0%, #c9b3e2 14%, var(--sky-pink) 24%, var(--sky-glow) 29%, var(--sea-far) 31%, var(--sea-mid) 55%, var(--sea-deep) 100%);
  }

  .top-bar {
    position: absolute; top: 0; left: 0; right: 0; height: 34px;
    display: flex; align-items: center; justify-content: space-between;
    padding: 0 70px; font-size: 11px; color: var(--ink);
  }
  .top-bar .contact-email, .top-bar .rating, .top-bar .phone { display: flex; align-items: center; gap: 6px; }
  .top-bar .right { display: flex; gap: 26px; }
  .rating-dot { width: 9px; height: 9px; border-radius: 50%; background: var(--orange); }
  .stars { letter-spacing: 1px; }
  .icon { width: 11px; height: 11px; }

  .main-nav {
    position: absolute; top: 40px; left: 62px; width: 1076px; height: 72px;
    display: flex; align-items: center;
    padding: 0 0 0 22px;
    background: rgba(255,255,255,.12);
    border: 1px solid rgba(255,255,255,.55);
    border-radius: 14px;
  }
  .brand { display: flex; align-items: center; gap: 8px; font-size: 22px; font-weight: 800; color: var(--orange); width: 245px; }
  .brand-mark { width: 14px; height: 14px; border-radius: 50%; background: var(--orange); }
  .nav-links { display: flex; gap: 20px; list-style: none; font-size: 13px; font-weight: 500; }
  .nav-links .active { color: var(--orange); }
  .quote-btn {
    position: absolute; right: -6px; top: -4px;
    width: 132px; height: 52px; border-radius: 6px;
    background: var(--orange); color: var(--white);
    display: flex; align-items: center; justify-content: center;
    font-size: 13px; font-weight: 500;
    box-shadow: 0 4px 10px rgba(240,145,44,.35);
  }

  .hero-rule { position: absolute; left: 0; top: 0; }

  .explore {
    position: absolute; left: 52px; top: 745px;
    transform: rotate(-90deg); transform-origin: left top;
    font-size: 84px; font-weight: 900; color: var(--white); letter-spacing: 2px; line-height: 1;
  }
  .more {
    position: absolute; left: 138px; top: 470px;
    transform: rotate(-90deg); transform-origin: left top;
    font-size: 64px; font-weight: 500; color: transparent;
    -webkit-text-stroke: 2px var(--white); letter-spacing: 2px; line-height: 1;
  }

  .slider-dots { position: absolute; left: 1132px; top: 345px; display: flex; flex-direction: column; gap: 8px; }
  .slider-dots span { width: 13px; height: 13px; border-radius: 50%; background: var(--orange); }
  .slider-dots span + span { width: 11px; height: 11px; margin-left: 1px; border: 2px solid var(--orange); background: var(--orange-mid); }

  .hero-intro {
    position: absolute; left: 852px; top: 525px; width: 290px; height: 118px;
    padding: 18px 14px; font-size: 10.5px; line-height: 1.65; color: var(--ink);
    background: rgba(255,255,255,.18);
    border: 1px solid rgba(255,255,255,.45); border-radius: 10px;
  }

  .hero-edge { position: absolute; left: 0; bottom: 0; }
</style>
</head>
<body>
<div class="site">
  <div class="hero-photo" role="img" aria-label="Red and white luxury motor yacht cruising across open sea at a pink sunset, with a white wake"></div>

  <header class="top-bar">
    <div class="contact-email">
      <svg class="icon" viewBox="0 0 12 12"><rect x="1" y="2.5" width="10" height="7" rx="1" fill="none" stroke="#F0912C" stroke-width="1.2"/><path d="M1.5 3l4.5 3.5L10.5 3" fill="none" stroke="#F0912C" stroke-width="1.2"/></svg>
      info@tkfinanceman.example
    </div>
    <div class="right">
      <div class="rating"><span class="rating-dot"></span>5.0 <span class="stars">★★★★★</span></div>
      <div class="phone">
        <svg class="icon" viewBox="0 0 12 12"><path d="M3 1l2 2.5-1.2 1.3a7 7 0 0 0 3.4 3.4L8.5 7 11 9l-1.2 1.8C5.5 10.5 1.5 6.5 1.2 2.2z" fill="#F0912C"/></svg>
        555-014-2290
      </div>
    </div>
  </header>

  <nav class="main-nav">
    <div class="brand"><span class="brand-mark"></span>TKFinanceMan</div>
    <ul class="nav-links">
      <li class="active">Home</li>
      <li>About us</li>
      <li>RV Loans</li>
      <li>Boat Loans</li>
      <li>FAQ</li>
      <li>News</li>
      <li>Affiliate Programs</li>
      <li>Contact Us</li>
    </ul>
    <div class="quote-btn">Get A Quote</div>
  </nav>

  <svg class="hero-rule" width="200" height="260" viewBox="0 0 200 260">
    <path d="M0 222 H170 V200" fill="none" stroke="#ffffff" stroke-width="2"/>
  </svg>

  <h1 class="explore">EXPLORE</h1>
  <div class="more">MORE</div>

  <div class="slider-dots"><span></span><span></span></div>

  <p class="hero-intro">We Specialize In Making Your Dreams Of Owning A Boat Or RV A Reality. Whether You're Looking To Explore Scenic Trails, Cruise Serene Waters, Or Create Unforgettable Memories, We're Here To Provide The Financial Support You Need.</p>

  <svg class="hero-edge" width="1200" height="200" viewBox="0 0 1200 200" preserveAspectRatio="none">
    <path d="M0 200 V150 C60 140 110 152 170 140 C240 126 300 138 370 122 C450 104 520 116 600 98 C680 82 760 92 840 76 C920 62 1000 66 1080 50 C1130 40 1170 34 1200 26 V200 Z" fill="#ffffff"/>
  </svg>
</div>
</body>
</html>
```